Holistic/ Sports Psychologist needs flyer design

I need a flyer designed that catches the attention of potential customers - (parents of young athletes and athletes) who may be looking for psychological services. I have a logo and all the relevant info for the flyer but would like someone to take it and make it look creative, fun, fresh and attention getting for high school and college athletes. The colors used can be from my logo design which represents my holistic approach.
Target Market(s)
high school and collegiate athletes
Industry/Entity Type
sports psychology
Requirements
Must have
- Info I put on the flyer with my logo and please add some graphics and color based on my logo

```html
<!DOCTYPE html>
<html lang="en">
<head>
<meta charset="utf-8">
<title>Holistic Psychology &amp; Sports Psychology Consulting</title>
<link href="https://fonts.googleapis.com/css2?family=Patrick+Hand&family=Dancing+Script:wght@700&family=Poppins:wght@400;500;700&display=swap" rel="stylesheet">
<style>
  :root{
    --title-green:#4d6a3c;
    --brand-purple:#6455a6;
    --brand-blue:#336aa3;
    --leaf-green:#aed17b;
    --sun-yellow:#f5c21c;
    --ink:#1d1d1d;
    --paper:#ffffff;
  }
  *{margin:0;padding:0;box-sizing:border-box}
  html,body{width:970px;height:1200px;overflow:hidden;background:var(--paper)}
  body{font-family:"Poppins",sans-serif;color:var(--ink)}
  .flyer{position:relative;width:970px;height:1200px;overflow:hidden;background:var(--paper)}
  .swoosh{position:absolute;left:0;top:0}
  .title{position:absolute;left:58px;top:44px;color:var(--title-green);font-family:"Patrick Hand",cursive;font-weight:400;font-size:68px;line-height:64px}
  .title .script{display:block;font-family:"Dancing Script",cursive;color:var(--brand-purple);font-size:84px;line-height:86px;margin-top:-2px}
  .brand{position:absolute;left:707px;top:56px;width:205px;text-align:center}
  .brand-dot{width:120px;height:120px;border-radius:50%;background:var(--brand-blue);margin:0 auto 8px}
  .brand-name{font-family:"Poppins",sans-serif;font-size:17px;line-height:22px;color:var(--brand-blue);font-weight:400}
  .brand-bar{height:14px;background:var(--leaf-green);margin-top:3px}
  .team-photo{position:absolute;left:520px;top:258px;width:450px;height:630px;
    background:linear-gradient(180deg,#e9e4dc 0%,#2a2a2a 30%,#1f1f1f 70%,#d9d9d9 100%);
    border-radius:140px 140px 20px 20px;opacity:.9}
  .services{position:absolute;left:59px;top:352px;width:440px}
  .services h2{font-weight:500;font-size:21.5px;line-height:30px;color:var(--ink);white-space:nowrap}
  .services h2 strong{color:var(--brand-purple);font-weight:700;font-size:25.5px}
  .service{margin-top:16px}
  .service-bar{display:flex;align-items:center;height:27px;width:368px}
  .service-icon{flex:none;width:30px;height:27px;display:flex;align-items:center;justify-content:center}
  .service-label{flex:1;height:27px;margin-left:4px;padding-left:18px;font-weight:700;font-size:18.5px;line-height:28px;white-space:nowrap;
    clip-path:polygon(4% 0,100% 0,97% 100%,0 100%)}
  .is-purple .service-icon{background:var(--leaf-green)}
  .is-purple .service-label{background:var(--brand-purple);color:#fff}
  .is-green .service-icon{background:var(--brand-purple)}
  .is-green .service-label{background:var(--leaf-green);color:var(--ink)}
  .service p{width:392px;font-size:13.8px;line-height:16.6px;margin-top:6px}
  .bottom-band{position:absolute;left:0;top:977px;width:970px;height:223px;background:var(--brand-purple)}
  .bio{position:absolute;left:55px;top:907px;width:857px;height:177px;background:var(--leaf-green);
    border:3px solid #fff;border-radius:12px;display:flex}
  .bio-photo{flex:none;width:196px;height:171px;border-radius:10px 0 0 10px;background:linear-gradient(160deg,#9fb2c4,#6d7f93 60%,#2c3470)}
  .bio-text{padding:16px 20px 0 35px;font-size:13.8px;line-height:16.4px}
  .bio-text p+p{margin-top:8px}
  .telehealth{position:absolute;left:59px;top:1086px;color:#fff;font-size:22px;line-height:30px;white-space:nowrap}
  .telehealth b{color:var(--sun-yellow);font-weight:700}
  .contact{position:absolute;left:59px;top:1128px;display:flex;align-items:center;gap:7px;color:#fff;font-size:13.4px;white-space:nowrap}
  .contact .label{color:var(--sun-yellow);font-weight:700;font-size:14px;margin-right:5px}
  .contact svg{flex:none}
  .contact span+svg{margin-left:4px}
</style>
</head>
<body>
<main class="flyer">
  <svg class="swoosh" width="970" height="600" viewBox="0 0 970 600" aria-hidden="true">
    <path d="M0 240 C150 330 380 330 520 250 C620 190 650 100 655 0 L718 0 C690 60 670 120 690 200 C705 260 740 290 760 330 L735 340 C700 300 670 280 640 260 C520 340 230 360 0 258 Z" fill="var(--brand-blue)"/>
    <path d="M970 235 C895 235 842 290 842 360 C842 430 895 480 970 480 L970 445 C915 445 880 405 880 360 C880 312 915 272 970 272 Z" fill="var(--brand-purple)"/>
  </svg>

  <h1 class="title">Holistic Psychology &amp;<br>Sports Psychology<span class="script">Consulting</span></h1>

  <div class="brand">
    <div class="brand-dot"></div>
    <div class="brand-name">Dr. Elena Whitfield</div>
    <div class="brand-bar"></div>
  </div>

  <div class="team-photo" role="img" aria-label="Photo of three young athletes in sportswear, one holding a volleyball"></div>

  <section class="services">
    <h2>Ways to Improve Athletic Performance<br>Using Sports &amp; <strong>Holistic Psychology</strong></h2>

    <div class="service is-purple">
      <div class="service-bar"><div class="service-icon"><svg width="16" height="16" viewBox="0 0 16 16"><circle cx="8" cy="6" r="4" fill="none" stroke="#1d1d1d" stroke-width="1.6"/><path d="M2 15h12" stroke="#1d1d1d" stroke-width="1.6"/></svg></div><div class="service-label">MENTAL SKILLS TRAINING</div></div>
      <p><b>Ex</b>: visualization, goal-setting, motivation, self- talk, mindset, concentration techniques</p>
    </div>

    <div class="service is-green">
      <div class="service-bar"><div class="service-icon"><svg width="16" height="16" viewBox="0 0 16 16"><path d="M3 15V10M7 15V7M11 15V4M15 15V2" stroke="#fff" stroke-width="2"/></svg></div><div class="service-label">PERFORMANCE ENHANCEMENT</div></div>
      <p>Eliminate psychological barriers that are hindering performance such as self- doubt, perfectionism, fear of failure, &amp; burnout</p>
    </div>

    <div class="service is-purple">
      <div class="service-bar"><div class="service-icon"><svg width="16" height="16" viewBox="0 0 16 16"><circle cx="8" cy="8" r="6" fill="#1d1d1d"/></svg></div><div class="service-label">MENTAL HEALTH</div></div>
      <p>Anxiety and stress management by using relaxation techniques, breathwork, and mindfulness practices</p>
    </div>

    <div class="service is-green">
      <div class="service-bar"><div class="service-icon"><svg width="16" height="16" viewBox="0 0 16 16"><circle cx="5" cy="4" r="2" fill="#fff"/><path d="M5 7v8M11 6v9M9 9h5" stroke="#fff" stroke-width="1.8"/></svg></div><div class="service-label">INJURY RECOVERY SUPPORT</div></div>
      <p>Assist athletes in maintaining resilience and positive mental attitude during rehabilitation as well as processing emotions relating to any potential trauma caused by the injury or life transitions resulting from it.</p>
    </div>

    <div class="service is-purple">
      <div class="service-bar"><div class="service-icon"><svg width="16" height="16" viewBox="0 0 16 16"><circle cx="8" cy="8" r="6" fill="#1d1d1d"/><circle cx="8" cy="9" r="2.5" fill="var(--leaf-green)"/></svg></div><div class="service-label">BURNOUT PREVENTION</div></div>
      <p>Teach athletes how to have balance in sports and life so they can experience longevity in their sports as well as overall optimal health and well-being.</p>
    </div>
  </section>

  <div class="bottom-band"></div>

  <section class="bio">
    <div class="bio-photo" role="img" aria-label="Portrait of the psychologist seated on a sandy beach"></div>
    <div class="bio-text">
      <p>Dr. Elena Whitfield is a licensed psychologist. She understands the unique experiences of athletes due to her background as an All-American swimmer, collegiate and age group swim coach, parent of a collegiate/professional athlete, and sports psychology researcher. She works with athletes to optimize performance and overall well-being.</p>
      <p>Her specializations include: performance anxiety, mental performance, stress management, anxiety, depressions, trauma, life transitions, relationship issues, injury, and sleep.</p>
    </div>
  </section>

  <p class="telehealth">All services are provided online <b>via telehealth</b>. Sessions are <b>30 or 55 minutes</b>.</p>

  <div class="contact">
    <span class="label">Contact info</span>
    <svg width="15" height="15" viewBox="0 0 16 16"><circle cx="8" cy="8" r="8" fill="var(--leaf-green)"/><path d="M5 4l2 2-1 1c.5 1.3 1.7 2.5 3 3l1-1 2 2-1.5 1.5C7.5 12 4 8.5 3.5 5.5Z" fill="var(--brand-purple)"/></svg>
    <span>555-014-2290</span>
    <svg width="15" height="15" viewBox="0 0 16 16"><circle cx="8" cy="8" r="8" fill="var(--leaf-green)"/><circle cx="8" cy="8" r="4.5" fill="none" stroke="var(--brand-purple)" stroke-width="1.3"/><path d="M3.5 8h9M8 3.5v9" stroke="var(--brand-purple)" stroke-width="1.1"/></svg>
    <span>www.drelenawhitfield.com</span>
    <svg width="15" height="15" viewBox="0 0 16 16"><circle cx="8" cy="8" r="8" fill="var(--leaf-green)"/><path d="M8 13s-3.5-3.6-3.5-6a3.5 3.5 0 0 1 7 0c0 2.4-3.5 6-3.5 6z" fill="var(--brand-purple)"/><circle cx="8" cy="7" r="1.3" fill="var(--leaf-green)"/></svg>
    <span>820 Harbor Lane #115</span>
    <svg width="15" height="15" viewBox="0 0 16 16"><circle cx="8" cy="8" r="8" fill="var(--leaf-green)"/><path d="M8 13s-3.5-3.6-3.5-6a3.5 3.5 0 0 1 7 0c0 2.4-3.5 6-3.5 6z" fill="var(--brand-purple)"/><circle cx="8" cy="7" r="1.3" fill="var(--leaf-green)"/></svg>
    <span>Seabrook Cove, FL 32000</span>
  </div>
</main>
</body>
</html>
```